Business card design for Virtual Assistance company

I need a business card designed for my virtual assistance company. We are a small company who services primarily C-level executive clients. The card needs to be double sided with the following contact information on the back:
Melissa Thornbury
Owner/CEO
info@rkpadvisory.net
www.rkpadvisory.net
555.302.9817

The front side should just have the company name incorporated: "RKP Advisory" and "virtual assistance"

The card should be simplistic, but eye catching and should speak to high level executives. Our primary focus areas consist of executive assistance and government contracting.

Target Market(s)

CEOs and executives

Contact Information for Business Card

see project description. phone, email, website.

Colors

Designer to choose only greyscale colors for use in the design.

```html
<!DOCTYPE html>
<html lang="en">
<head>
<meta charset="utf-8">
<title>RKP Advisory – Business Card</title>
<link rel="stylesheet" href="https://fonts.googleapis.com/css2?family=Cinzel:wght@600&family=Poppins:wght@400;500&display=swap">
<style>
  :root {
    --ink: #2b2d31;
    --ink-light: #3c3f44;
    --ink-dark: #1f2023;
    --white: #ffffff;
    --paper-grey: #b9bcc2;
    --backdrop: #d9d9db;
    --serif: "Cinzel", "Times New Roman", serif;
    --sans: "Poppins", "Helvetica Neue", Arial, sans-serif;
  }
  * { box-sizing: border-box; margin: 0; padding: 0; }
  html, body {
    width: 1200px; height: 866px; overflow: hidden;
    background: var(--backdrop);
  }
  .sheet {
    width: 1200px; height: 866px;
    display: flex; flex-direction: column;
    align-items: center; justify-content: center; gap: 40px;
  }
  .card {
    position: relative;
    width: 660px; height: 377px;
    overflow: hidden;
    box-shadow: 0 10px 26px rgba(0,0,0,.3);
  }

  /* Front */
  .card--front {
    background: linear-gradient(135deg, var(--ink-dark) 0%, var(--ink) 50%, var(--ink-light) 100%);
    display: flex; flex-direction: column; align-items: center; justify-content: center;
    color: var(--white);
  }
  .brand-name {
    font-family: var(--serif); font-weight: 600;
    font-size: 50px; letter-spacing: 4px; line-height: 1;
    text-transform: uppercase;
  }
  .brand-tagline {
    margin-top: 16px;
    display: flex; align-items: center; gap: 14px;
    font-family: var(--sans); font-weight: 500;
    font-size: 15px; letter-spacing: 4px; text-transform: uppercase;
  }
  .brand-tagline::before, .brand-tagline::after {
    content: ""; width: 34px; height: 2px; background: var(--white);
  }

  /* Back */
  .card--back { background: var(--white); color: var(--ink); }
  .person {
    position: absolute; left: 34px; top: 40px;
  }
  .person__name {
    font-family: var(--serif); font-weight: 600;
    font-size: 25px; letter-spacing: 1.5px; line-height: 1.2; text-transform: uppercase;
  }
  .person__title {
    font-family: var(--sans); font-size: 17px; margin-top: 2px;
  }
  .contact {
    position: absolute; left: 34px; top: 124px;
    list-style: none;
    font-family: var(--sans); font-size: 17px; line-height: 1.5;
  }
  .contact li { display: flex; align-items: center; gap: 8px; }
  .contact svg { width: 16px; height: 16px; fill: var(--ink); flex: none; }
  .back-brand {
    position: absolute; right: 40px; top: 150px;
    font-family: var(--serif); font-weight: 600;
    font-size: 34px; letter-spacing: 2px; line-height: 1; text-transform: uppercase;
  }
  .divider {
    position: absolute; left: 34px; right: 40px; top: 214px;
    height: 1px; background: var(--ink);
  }
  .website {
    position: absolute; right: 40px; top: 232px;
    font-family: var(--sans); font-size: 17px; letter-spacing: .5px;
  }
  .footer-band {
    position: absolute; left: 0; bottom: 0; width: 100%; height: 80px;
  }
  .footer-tagline {
    position: absolute; right: 40px; bottom: 10px;
    font-family: var(--sans); font-weight: 500;
    font-size: 15px; letter-spacing: 2px; line-height: 1.3; text-transform: uppercase;
    color: var(--white);
  }
</style>
</head>
<body>
<main class="sheet">
  <section class="card card--front" aria-label="Card front">
    <div class="brand-name">RKP Advisory</div>
    <div class="brand-tagline">Virtual Assistance</div>
  </section>

  <section class="card card--back" aria-label="Card back">
    <div class="person">
      <div class="person__name">Melissa Thornbury</div>
      <div class="person__title">Owner/CEO</div>
    </div>
    <ul class="contact">
      <li>
        <svg viewBox="0 0 24 24" aria-hidden="true"><path d="M6.6 10.8a15.1 15.1 0 0 0 6.6 6.6l2.2-2.2a1 1 0 0 1 1-.25 11.4 11.4 0 0 0 3.6.57 1 1 0 0 1 1 1V20a1 1 0 0 1-1 1A17 17 0 0 1 3 4a1 1 0 0 1 1-1h3.5a1 1 0 0 1 1 1c0 1.25.2 2.45.57 3.57a1 1 0 0 1-.25 1z"/></svg>
        555.302.9817
      </li>
      <li>
        <svg viewBox="0 0 24 24" aria-hidden="true"><path d="M2 5h20v14H2z M3.5 6.5 12 13l8.5-6.5" fill="var(--ink)" stroke="var(--white)" stroke-width="1.4"/></svg>
        info@rkpadvisory.net
      </li>
    </ul>
    <div class="back-brand">RKP Advisory</div>
    <div class="divider"></div>
    <div class="website">www.rkpadvisory.net</div>
    <svg class="footer-band" viewBox="0 0 660 80" preserveAspectRatio="none" aria-hidden="true">
      <path d="M0 64 H250 C275 64 275 58 290 58 V80 H0 Z" fill="var(--paper-grey)"/>
      <path d="M0 70 H255 C285 70 280 44 315 44 H660 V80 H0 Z" fill="var(--ink)"/>
    </svg>
    <div class="footer-tagline">Virtual Assistance</div>
  </section>
</main>
</body>
</html>
```